Birchline Septic Solutions

Would like to see some single sided ones but would also like to see some double sided with one sided only being the logo. Owners name is Colin Vandro. Phone number is 555-214-0387
Services are pumping, inspections, installs, and repairs

Contact Information for Business Card

555-241-0387 Colin Vandro Ashford Falls, OH

```html
<!DOCTYPE html>
<html lang="en">
<head>
<meta charset="utf-8">
<title>Birchline Septic Solutions – Business Cards</title>
<link rel="stylesheet" href="https://fonts.googleapis.com/css2?family=Montserrat:wght@400;500;700;800&display=swap">
<style>
  :root{
    --ink:#0b0b0b;
    --paper:#ffffff;
    --teal:#1fb8b0;
    --stage:#d9d9d9;
    --muted:#222222;
  }
  *{box-sizing:border-box;margin:0;padding:0}
  html,body{width:1200px;height:856px;overflow:hidden}
  body{
    background:var(--stage);
    font-family:"Montserrat",sans-serif;
    display:flex;flex-direction:column;align-items:center;justify-content:center;gap:36px;
  }
  .card{
    position:relative;width:665px;height:380px;overflow:hidden;
    box-shadow:0 10px 28px rgba(0,0,0,.28);
  }
  /* front */
  .card--front{background:var(--paper);color:var(--ink)}
  .front__sweep{position:absolute;inset:0;width:100%;height:100%}
  .sweep__dark{fill:var(--ink)}
  .sweep__accent{fill:var(--teal)}
  .brand{display:flex;align-items:center;gap:12px}
  .brand__mark{width:16px;height:16px;background:var(--teal);flex:none}
  .brand__name{font-weight:800;font-size:27px;line-height:1.1;letter-spacing:.02em;text-transform:uppercase}
  .card--front .brand{position:absolute;left:42px;top:80px;width:270px;color:var(--ink)}
  .front__divider{position:absolute;left:330px;top:56px;width:2px;height:120px;background:var(--teal)}
  .contact{position:absolute;left:352px;top:56px;width:250px;font-size:15px;line-height:1.35}
  .contact__name{font-weight:800;font-size:19px;text-transform:uppercase;letter-spacing:.01em}
  .contact__name .surname{color:var(--teal)}
  .contact__role{font-weight:400;margin-bottom:8px;color:var(--muted)}
  .contact__line{display:flex;align-items:center;gap:7px;font-weight:500}
  .contact__line svg{width:14px;height:14px;fill:var(--teal);flex:none}
  .contact__address{font-weight:500;padding-left:21px}
  /* back */
  .card--back{background:var(--ink);color:var(--paper);display:flex;flex-direction:column;align-items:center;justify-content:center;gap:34px}
  .card--back .brand{color:var(--paper)}
  .card--back .brand__name{font-size:36px;text-align:center}
  .services{font-size:19px;font-weight:500;text-align:center;line-height:1.45}
  .services__item{display:inline-flex;align-items:center;gap:6px;margin:0 5px}
  .tick{width:17px;height:17px;fill:none;stroke:var(--paper);stroke-width:2.2;stroke-linecap:round;stroke-linejoin:round}
</style>
</head>
<body>

<section class="card card--front" aria-label="Business card front">
  <svg class="front__sweep" viewBox="0 0 665 380" preserveAspectRatio="none" aria-hidden="true">
    <path class="sweep__dark" d="M0,380 L0,372 L440,262 C478,252 492,236 502,218 C514,198 530,194 560,188 L665,160 L665,380 Z"/>
    <path class="sweep__accent" d="M0,362 L0,350 L458,228 C452,246 440,254 422,260 Z"/>
  </svg>
  <div class="brand">
    <span class="brand__mark"></span>
    <span class="brand__name">Birchline Septic Solutions</span>
  </div>
  <div class="front__divider"></div>
  <div class="contact">
    <p class="contact__name">Colin <span class="surname">Vandro</span></p>
    <p class="contact__role">Owners</p>
    <p class="contact__line">
      <svg viewBox="0 0 24 24"><path d="M6.6 10.8a15.1 15.1 0 0 0 6.6 6.6l2.2-2.2a1 1 0 0 1 1-.25 11.4 11.4 0 0 0 3.6.57 1 1 0 0 1 1 1V20a1 1 0 0 1-1 1A17 17 0 0 1 3 4a1 1 0 0 1 1-1h3.5a1 1 0 0 1 1 1c0 1.25.2 2.45.57 3.57a1 1 0 0 1-.25 1z"/></svg>
      555-214-0387
    </p>
    <p class="contact__address">555-241-0387 Colin<br>Vandro Ashford Falls, OH</p>
  </div>
</section>

<section class="card card--back" aria-label="Business card back">
  <div class="brand">
    <span class="brand__mark"></span>
    <span class="brand__name">Birchline<br>Septic Solutions</span>
  </div>
  <div class="services">
    <span class="services__item"><svg class="tick" viewBox="0 0 20 20"><circle cx="10" cy="10" r="8"/><path d="M6.5 10.2l2.4 2.4 4.6-5"/></svg>Services are pumping</span><br>
    <span class="services__item"><svg class="tick" viewBox="0 0 20 20"><circle cx="10" cy="10" r="8"/><path d="M6.5 10.2l2.4 2.4 4.6-5"/></svg>inspections</span>
    <span class="services__item"><svg class="tick" viewBox="0 0 20 20"><circle cx="10" cy="10" r="8"/><path d="M6.5 10.2l2.4 2.4 4.6-5"/></svg>installs</span>
    <span class="services__item"><svg class="tick" viewBox="0 0 20 20"><circle cx="10" cy="10" r="8"/><path d="M6.5 10.2l2.4 2.4 4.6-5"/></svg>and repairs</span>
  </div>
</section>

</body>
</html>
```